Veldmark Supplies Business Card

Professional business card that stand out to our potential customers. Front and back with clean modern design

Industry/Entity Type

Oil and gas

Contact Information for Business Card

Name, address, website , office phone and cell number

Requirements
Must have
• Editable files for each employee

```html
<!DOCTYPE html>
<html lang="en">
<head>
<meta charset="utf-8">
<title>Veldmark Supplies Business Card</title>
<link href="https://fonts.googleapis.com/css2?family=Montserrat:wght@400;500;700;800&display=swap" rel="stylesheet">
<style>
  :root {
    --backdrop: #2b2b2b;
    --card-blue: #0bb1d3;
    --card-blue-deep: #0a93b2;
    --brand-red: #e8202a;
    --brand-blue: #12a9cf;
    --ink: #1d1d1f;
    --paper: #ffffff;
  }
  * { box-sizing: border-box; margin: 0; padding: 0; }
  html, body { width: 1200px; height: 875px; overflow: hidden; }
  body {
    background: var(--backdrop);
    font-family: "Montserrat", sans-serif;
    display: flex;
    align-items: center;
    justify-content: center;
    gap: 50px;
  }
  .card {
    position: relative;
    width: 525px;
    height: 300px;
    border-radius: 18px;
    overflow: hidden;
    box-shadow: 0 18px 40px rgba(0,0,0,.45);
  }

  /* Back side */
  .card-back {
    background: var(--card-blue);
    display: flex;
    align-items: center;
    justify-content: center;
    gap: 14px;
  }
  .card-back .brand-mark {
    width: 26px; height: 26px;
    background: var(--card-blue-deep);
  }
  .card-back .brand-name {
    font-weight: 800;
    font-size: 30px;
    letter-spacing: .06em;
    text-transform: uppercase;
    color: var(--card-blue-deep);
  }

  /* Front side */
  .card-front { background: var(--paper); }
  .front-brand {
    position: absolute;
    left: 28px; top: 98px;
    width: 200px;
    display: flex;
    flex-direction: column;
    align-items: center;
    gap: 12px;
  }
  .front-brand .brand-mark {
    width: 40px; height: 40px;
    background: var(--brand-blue);
  }
  .front-brand .brand-name {
    font-weight: 800;
    font-size: 21px;
    letter-spacing: .05em;
    text-transform: uppercase;
    color: var(--brand-red);
    text-align: center;
    line-height: 1.15;
  }
  .divider {
    position: absolute;
    left: 246px; top: 48px;
    width: 1.5px; height: 168px;
    background: var(--brand-red);
  }
  .contact {
    position: absolute;
    left: 264px; top: 46px;
    color: var(--ink);
  }
  .person-name {
    font-weight: 700;
    font-size: 22px;
    color: var(--brand-red);
    line-height: 1.1;
  }
  .person-title {
    font-size: 12px;
    margin: 3px 0 12px;
  }
  .contact-list { list-style: none; }
  .contact-list li {
    display: flex;
    align-items: center;
    gap: 7px;
    font-size: 11.5px;
    line-height: 1.75;
  }
  .contact-list svg { width: 11px; height: 11px; fill: var(--brand-blue); flex: none; }
  .address {
    margin-top: 10px;
    font-size: 11.5px;
    line-height: 1.4;
  }
  .bands { position: absolute; inset: 0; width: 525px; height: 300px; }
</style>
</head>
<body>

<section class="card card-back" aria-label="Card back">
  <span class="brand-mark"></span>
  <span class="brand-name">Veldmark Supplies</span>
</section>

<section class="card card-front" aria-label="Card front">
  <svg class="bands" viewBox="0 0 525 300" aria-hidden="true">
    <polygon points="0,288 338,272 326,300 0,300" fill="var(--brand-blue)"/>
    <polygon points="350,271 525,212 525,300 337,300" fill="var(--brand-red)"/>
  </svg>

  <div class="front-brand">
    <span class="brand-mark"></span>
    <span class="brand-name">Veldmark<br>Supplies</span>
  </div>

  <div class="divider"></div>

  <div class="contact">
    <h1 class="person-name">Tomas Reyner</h1>
    <p class="person-title">President</p>
    <ul class="contact-list">
      <li><svg viewBox="0 0 24 24"><path d="M4 8c0-3 4-5 8-5s8 2 8 5l-3 2-2-3H9L7 10zM6 11h12v9H6z"/></svg>+1.555.210.4400 x123</li>
      <li><svg viewBox="0 0 24 24"><path d="M6 2l4 5-2 3c1 3 3 5 6 6l3-2 5 4-3 4C10 21 3 14 2 5z"/></svg>+1.555.123.456</li>
      <li><svg viewBox="0 0 24 24"><path d="M2 5h20v14H2zM3 6l9 7 9-7"/></svg>info@veldmarksupplies.com</li>
      <li><svg viewBox="0 0 24 24"><circle cx="12" cy="12" r="10"/></svg>www.veldmarksupplies.com</li>
    </ul>
    <p class="address">42 Harbor Point Drive<br>Millbrook, NJ 07000 USA</p>
  </div>
</section>

</body>
</html>
```